Profesional personal website needs design and business card

I need a business card with my professional name as a logo "Dorian Vitality" for my business. I am a Wellness Coach, consultant and trainer. So it should be professional, wellness oriented and modern.

Target Market(s)

Private clients, governments, corporations. Luxury and high market.

Industry/Entity Type

Health And Wellness

Contact Information for Business Card

Dorian Vitality should be the logo

Colors

Designer to choose colors to be used in the design.

Requirements
Must have
• Dorian Vitality
• Name: Tomás Lirandel
• Wellness Coach, Consultant & Trainer.
• Website: www.dorianvitality-example.com
• Phone:
• Spain (+34) 612 480 317
• (USA) +1 (555) 610 4829
Nice to have
• The most important is the design of "Dorian Vitality", as this is going to be my personal brand logo. It should be professional, wellness, high end and actual.
Should not have
• no golds, no baroque style..

```html
<!DOCTYPE html>
<html lang="en">
<head>
<meta charset="utf-8">
<title>Dorian Vitality – Business Card</title>
<link rel="stylesheet" href="https://fonts.googleapis.com/css2?family=Montserrat:wght@500;600&family=Roboto:wght@400&display=swap">
<style>
  :root {
    --brand-green: #7aad3c;
    --brand-green-dark: #6a9c30;
    --ink-grey: #555555;
    --rule-grey: #6e6e6e;
    --card-white: #ffffff;
    --backdrop: #d9d9d6;
  }
  * { box-sizing: border-box; margin: 0; padding: 0; }
  html, body { width: 1200px; height: 801px; overflow: hidden; }
  body {
    background: var(--backdrop);
    font-family: "Roboto", Arial, sans-serif;
    position: relative;
  }
  .card {
    position: absolute;
    top: 258px;
    width: 500px;
    height: 286px;
    border-radius: 3px;
    box-shadow: 0 10px 24px rgba(0,0,0,0.18);
    overflow: hidden;
  }
  .card--front { left: 60px; background: var(--card-white); }
  .card--back { left: 640px; background: var(--brand-green); }

  /* Front */
  .front-brand {
    position: absolute;
    left: 0; top: 0;
    width: 230px; height: 100%;
    display: flex; flex-direction: column;
    align-items: center; justify-content: center;
    gap: 14px;
  }
  .brand-dot {
    width: 62px; height: 62px;
    border-radius: 50%;
    background: var(--brand-green);
  }
  .brand-name {
    font-family: "Montserrat", sans-serif;
    font-weight: 500;
    letter-spacing: 0.04em;
    text-transform: uppercase;
    color: var(--brand-green);
    font-size: 19px;
    white-space: nowrap;
  }
  .divider {
    position: absolute;
    left: 232px; top: 70px;
    width: 1.5px; height: 146px;
    background: var(--rule-grey);
  }
  .front-contact {
    position: absolute;
    left: 252px; top: 70px;
    width: 240px;
  }
  .person-name {
    font-family: "Montserrat", sans-serif;
    font-weight: 600;
    color: var(--brand-green);
    font-size: 21px;
    line-height: 1.1;
  }
  .person-role {
    color: var(--ink-grey);
    font-size: 10.5px;
    margin: 3px 0 12px;
  }
  .contact-list { list-style: none; }
  .contact-item {
    display: flex; align-items: center; gap: 7px;
    color: var(--ink-grey);
    font-size: 12.5px;
    line-height: 22px;
    white-space: nowrap;
  }
  .contact-icon { width: 12px; height: 12px; flex: none; fill: var(--brand-green); }

  /* Back */
  .back-map {
    position: absolute;
    left: 90px; top: 20px;
    width: 400px; height: 250px;
    background: radial-gradient(ellipse at 60% 45%, rgba(255,255,255,0.14), rgba(255,255,255,0.04) 65%, rgba(255,255,255,0) 80%);
  }
  .back-brand {
    position: absolute; inset: 0;
    display: flex; flex-direction: column;
    align-items: center; justify-content: center;
    gap: 18px;
  }
  .back-ring {
    width: 96px; height: 96px;
    border-radius: 50%;
    border: 3px solid var(--card-white);
  }
  .back-name {
    font-family: "Montserrat", sans-serif;
    font-weight: 500;
    letter-spacing: 0.04em;
    text-transform: uppercase;
    color: var(--card-white);
    font-size: 34px;
    white-space: nowrap;
  }
</style>
</head>
<body>

<section class="card card--front" aria-label="Business card front">
  <div class="front-brand">
    <span class="brand-dot"></span>
    <span class="brand-name">Dorian Vitality</span>
  </div>
  <div class="divider"></div>
  <div class="front-contact">
    <h1 class="person-name">Tomás Lirandel</h1>
    <p class="person-role">Wellness Coach, Consultant &amp; Trainer</p>
    <ul class="contact-list">
      <li class="contact-item">
        <svg class="contact-icon" viewBox="0 0 24 24"><path d="M6.6 10.8a15.1 15.1 0 0 0 6.6 6.6l2.2-2.2c.3-.3.7-.4 1-.2 1.1.4 2.3.6 3.6.6.6 0 1 .4 1 1V20c0 .6-.4 1-1 1A17 17 0 0 1 3 4c0-.6.4-1 1-1h3.5c.6 0 1 .4 1 1 0 1.3.2 2.5.6 3.6.1.3 0 .7-.2 1z"/></svg>
        (+34) 612 480 317 (Spain)
      </li>
      <li class="contact-item">
        <svg class="contact-icon" viewBox="0 0 24 24"><path d="M6.6 10.8a15.1 15.1 0 0 0 6.6 6.6l2.2-2.2c.3-.3.7-.4 1-.2 1.1.4 2.3.6 3.6.6.6 0 1 .4 1 1V20c0 .6-.4 1-1 1A17 17 0 0 1 3 4c0-.6.4-1 1-1h3.5c.6 0 1 .4 1 1 0 1.3.2 2.5.6 3.6.1.3 0 .7-.2 1z"/></svg>
        +1 (555) 610 4829 (USA)
      </li>
      <li class="contact-item">
        <svg class="contact-icon" viewBox="0 0 24 24"><path d="M2 5h20v14H2z M3.5 6.5 12 13l8.5-6.5" fill="none" stroke="#7aad3c" stroke-width="2"/></svg>
        info@dorianvitality-example.com
      </li>
      <li class="contact-item">
        <svg class="contact-icon" viewBox="0 0 24 24"><circle cx="12" cy="12" r="10"/><path d="M2 12h20M12 2c3 3 3 17 0 20M12 2c-3 3-3 17 0 20" fill="none" stroke="#fff" stroke-width="1.4"/></svg>
        www.dorianvitality-example.com
      </li>
    </ul>
  </div>
</section>

<section class="card card--back" aria-label="Business card back">
  <div class="back-map" role="img" aria-label="Faint dotted world map pattern"></div>
  <div class="back-brand">
    <span class="back-ring"></span>
    <span class="back-name">Dorian Vitality</span>
  </div>
</section>

</body>
</html>
```